Graphical design for food product in 1 Liter carton

We need this design not for a real product but as a showcase for a new service.

This special situation makes it really simple for you to participate because you only have to care about how the visual impression of your design is.

Furthermore it gives you the opportunity to get an extra winning chance if you choose to also participate in the open competition at our website - where you can enter the same design as you enter here at ArtRally.

Here is the requirements:

1. You must apply your design to our attatched template

2. Make a design for a food product of your own choice, which is to be sold from retail stores in a rectangular 1 L carton – based on our template.

3. You are only allowed to use brand names and/or logos that you have the rights to use for this competition, so please make completely fictive brand names and logos.

4. Your design is evaluated on the visual impression only, which means that your text on the design can be in any language and doesn’t have to relate to the design.

5. The criteria for the evaluation of your design is your creativity, the graphical quality and how well the product will display it self in the stores.

If you also want to participate in the open competition on our website - where you can win an Lumatab Lite, and will get your design skills exposed to brand owners and packaging manufacturers all over the world, then please visit spinoframe.com/packaging-design-competition/

Attatched is:

A. Empty design template you must apply your design to. Remove the layer with our template when you return your send in your design.

B. Example of design applied to the template.

C. Example of the applied example design after it has been converted to 3D with our online 3D engine at SpinoFrame.com.

The winning design will be converted to 3D and will be used as a showcase on our website - all designers can enter their design to our open competition at SpinoFrame.com.

```html
<!DOCTYPE html>
<html lang="en">
<head>
<meta charset="utf-8">
<title>Iced Coffee – Ethiopian Blend carton</title>
<link rel="stylesheet" href="https://fonts.googleapis.com/css2?family=Jost:wght@300;400&display=swap">
<style>
  :root {
    --backdrop: #ececec;
    --carton-white: #ffffff;
    --fold-line: #d6d6d6;
    --coffee-orange: #b5651d;
    --coffee-orange-soft: #c98a4f;
    --ink: #2b2b2b;
    --band-black: #262626;
    --band-text: #ffffff;
  }
  html, body {
    margin: 0;
    padding: 0;
    width: 983px;
    height: 1200px;
    overflow: hidden;
    background: var(--backdrop);
  }
  .carton-net {
    position: absolute;
    left: 221px;
    top: 60px;
    width: 540px;
    height: 1080px;
    display: flex;
    box-shadow: 0 2px 10px rgba(0,0,0,0.08);
  }
  .panel {
    height: 1080px;
    background: var(--carton-white);
  }
  .panel-side { width: 220px; border-right: 1px solid var(--fold-line); }
  .panel-front { width: 320px; }
  .panel svg { display: block; }
  .pattern-fill { fill: url(#coffee-tone); }
  .motif-fill { fill: var(--coffee-orange); }
  .tagline {
    font-family: "Jost", sans-serif;
    font-weight: 400;
    font-size: 20px;
    fill: var(--ink);
  }
  .product-name {
    font-family: "Jost", sans-serif;
    font-weight: 300;
    font-size: 64px;
    fill: var(--ink);
  }
  .band { fill: var(--band-black); }
  .band-label {
    font-family: "Jost", sans-serif;
    font-weight: 400;
    font-size: 24px;
    fill: var(--band-text);
  }
</style>
</head>
<body>
<div class="carton-net">

  <section class="panel panel-side" aria-label="Side panel">
    <svg width="220" height="1080" viewBox="0 0 220 1080">
      <g class="side-message">
        <text class="tagline" x="110" y="245" text-anchor="middle">Iced Coffee begins</text>
        <text class="tagline" x="110" y="270" text-anchor="middle">with great Beans</text>
        <rect class="motif-fill" x="72" y="300" width="76" height="36" role="img" aria-label="Small coffee-bean block motif"/>
      </g>
      <g class="side-message">
        <text class="tagline" x="110" y="490" text-anchor="middle">Iced Coffee begins</text>
        <text class="tagline" x="110" y="515" text-anchor="middle">with great Beans</text>
        <rect class="motif-fill" x="72" y="545" width="76" height="36" role="img" aria-label="Small coffee-bean block motif"/>
      </g>
      <g class="side-message">
        <text class="tagline" x="110" y="775" text-anchor="middle">Iced Coffee begins</text>
        <text class="tagline" x="110" y="800" text-anchor="middle">with great Beans</text>
        <rect class="motif-fill" x="72" y="830" width="76" height="36" role="img" aria-label="Small coffee-bean block motif"/>
      </g>
    </svg>
  </section>

  <section class="panel panel-front" aria-label="Front panel">
    <svg width="320" height="1080" viewBox="0 0 320 1080">
      <defs>
        <linearGradient id="coffee-tone" x1="0" y1="0" x2="0" y2="1">
          <stop offset="0" stop-color="var(--coffee-orange-soft)"/>
          <stop offset="1" stop-color="var(--coffee-orange)"/>
        </linearGradient>
      </defs>

      <text class="product-name" transform="translate(80 820) rotate(-90)" textLength="740" lengthAdjust="spacing">ICED COFFEE</text>

      <g class="pattern-area" role="img" aria-label="Decorative pattern of coffee-coloured squares rising toward the top right">
        <rect class="pattern-fill" x="175" y="28" width="130" height="810"/>
        <rect class="pattern-fill" x="97" y="912" width="208" height="126"/>
      </g>

      <rect class="band" x="14" y="848" width="291" height="50"/>
      <text class="band-label" x="159" y="882" text-anchor="middle">ETHIOPIAN BLEND</text>

      <rect class="band" x="14" y="990" width="146" height="48"/>
      <text class="band-label" x="28" y="1022">1 Litre</text>
    </svg>
  </section>

</div>
</body>
</html>
```